Berufora Banner Design (Profilbanner und Unternehmensbanner) (1584 x 396) (1128 x 191)
Zielgruppe
Ich bin Dienstleister und Unternehmensberater für technischen B2B Vertrieb.
Für meinen Berufora Account suche ich einen Banner für meine Profilseite und einen Banner für die Unternehmensseite). Meine Zielgruppe sind leitende Angestellte in Unternehmen. Das Design sollte entsprechend grafisch hochwertig, seriös gestaltet sein.
I am a service provider and management consultant for technical B2B sales.
For my Berufora account, I'm looking for a banner for my profile page and a banner for the company page). My target group are executives in companies. The design should have a correspondingly high-quality graphic design and be serious.
Aufgabenstellung
Wichtig ist die Berücksichtigung meines Logos (PNG im Anhang) und des Corporate Identity Farben (PDF Anhang und unten stehend). Stock Bilder oder Grafiken können/sollen gerne mit eingebunden werden. Wichtig ist hier der passende Gesamteindruck.
It is important to consider my logo (PNG in the attachment) and the corporate identity colors (PDF attachment and below). Stock images or graphics can/should be included. The right overall impression is important here.
HEX / HTML 002854
HEX / HTML 00b6e3
Bannergrößen / Banner sizes
Profilbanner (1584 x 396)
Unternehmensseitenbanner (1128 x 191)

```html
<!DOCTYPE html>
<html lang="de">
<head>
<meta charset="utf-8">
<title>Lennart Wiesmann – Berufora Unternehmensseite</title>
<link rel="stylesheet" href="https://fonts.googleapis.com/css2?family=Titillium+Web:wght@400;600;700&family=Fira+Sans:wght@400;500&display=swap">
<style>
  :root {
    --navy: #002854;
    --navy-deep: #16284a;
    --brand-blue: #0a6fb5;
    --brand-cyan: #00b6e3;
    --photo-dark: #0d1c33;
    --white: #ffffff;
    --ink: #1f1f1f;
    --ink-soft: #3d3d3d;
    --ink-muted: #6b6b6b;
    --action: #0a66c2;
    --outline: #5f5f5f;
  }
  * { box-sizing: border-box; margin: 0; padding: 0; }
  html, body { width: 1200px; height: 656px; overflow: hidden; background: var(--white); }
  .page { position: relative; width: 1200px; height: 656px; font-family: "Fira Sans", sans-serif; }

  .banner { position: absolute; left: 0; top: 0; width: 1200px; height: 303px; overflow: hidden; }
  .banner__photo { position: absolute; inset: 0; }
  .banner__panel { position: absolute; inset: 0; }

  .headline { position: absolute; left: 96px; top: 60px; font-family: "Titillium Web", sans-serif; color: var(--white); line-height: 1; }
  .headline__line { display: block; white-space: nowrap; }
  .headline__line--one { font-size: 40px; font-weight: 400; }
  .headline__line--two { font-size: 40px; font-weight: 400; margin: 12px 0 0 39px; }
  .headline strong { font-weight: 700; font-size: 46px; }

  .contact { position: absolute; left: 221px; top: 262px; display: flex; align-items: center; gap: 20px;
    font-family: "Titillium Web", sans-serif; font-weight: 600; font-size: 15px; color: var(--white); letter-spacing: 0.2px; }
  .contact__item { display: flex; align-items: center; gap: 9px; }
  .contact__item svg { width: 24px; height: 24px; }

  .brand-tile { position: absolute; left: 39px; top: 213px; width: 166px; height: 164px; background: var(--navy-deep);
    display: flex; align-items: center; justify-content: center; text-align: center;
    font-family: "Titillium Web", sans-serif; font-weight: 700; font-size: 23px; line-height: 1.1; color: var(--brand-cyan); }

  .company { position: absolute; left: 35px; top: 398px; }
  .company__name { font-size: 36px; font-weight: 500; color: var(--ink); letter-spacing: 0.2px; line-height: 1; }
  .company__tagline { margin-top: 11px; font-size: 22px; color: var(--ink-soft); line-height: 1; }
  .company__meta { margin-top: 10px; font-size: 19px; color: var(--ink-muted); line-height: 1; white-space: nowrap; }
  .company__staff { margin-top: 26px; font-size: 22px; font-weight: 500; color: var(--ink-muted); line-height: 1; }

  .actions { position: absolute; left: 35px; top: 583px; display: flex; gap: 13px; }
  .btn { height: 49px; border-radius: 25px; display: flex; align-items: center; justify-content: center; gap: 10px;
    font-size: 24px; font-weight: 500; }
  .btn--follow { width: 210px; background: var(--action); color: var(--white); }
  .btn--website { width: 292px; border: 2px solid var(--action); color: var(--action); }
  .btn--more { width: 110px; border: 1.5px solid var(--outline); color: var(--ink-muted); }
  .btn svg { width: 22px; height: 22px; }
</style>
</head>
<body>
<main class="page">
  <section class="banner">
    <div class="banner__photo" role="img" aria-label="Stockfoto eines Automotors mit Riemenscheiben vor dunkelblauem Wabenhintergrund"
      style="background: radial-gradient(ellipse at 78% 45%, #5b6470 0%, #2a3340 25%, var(--photo-dark) 60%), var(--photo-dark);"></div>
    <svg class="banner__panel" width="1200" height="303" viewBox="0 0 1200 303" aria-hidden="true">
      <defs>
        <linearGradient id="panelFill" x1="0" y1="0" x2="1" y2="0.4">
          <stop offset="0" stop-color="#0b3d78"/>
          <stop offset="0.55" stop-color="#0a6fb5"/>
          <stop offset="1" stop-color="#1a8fd0"/>
        </linearGradient>
      </defs>
      <polygon points="0,0 495,0 630,232 585,303 0,303" fill="url(#panelFill)"/>
      <polygon points="495,0 630,232 585,303 575,303 620,232 485,0" fill="#00b6e3" opacity="0.35"/>
    </svg>

    <h1 class="headline">
      <span class="headline__line headline__line--one">VOLLE <strong>POWER</strong></span>
      <span class="headline__line headline__line--two">FÜR IHR <strong>BUSINESS</strong>.</span>
    </h1>

    <div class="contact">
      <span class="contact__item">
        <svg viewBox="0 0 24 24" fill="none" stroke="currentColor" stroke-width="1.6" stroke-linejoin="round">
          <path d="M5 3h4l2 5-2.5 1.5a11 11 0 0 0 6 6L16 13l5 2v4a2 2 0 0 1-2 2A16 16 0 0 1 3 5a2 2 0 0 1 2-2z"/>
        </svg>
        0987 | 654 321 0
      </span>
      <span class="contact__item">
        <svg viewBox="0 0 24 24" fill="none" stroke="currentColor" stroke-width="1.5">
          <circle cx="12" cy="12" r="10"/><ellipse cx="12" cy="12" rx="4.5" ry="10"/>
          <path d="M2 12h20M4 7h16M4 17h16M12 2v20"/>
        </svg>
        LENNARTWIESMANN.DE
      </span>
    </div>
  </section>

  <div class="brand-tile">Lennart<br>Wiesmann</div>

  <section class="company">
    <h2 class="company__name">Lennart Wiesmann Management &amp; Sales Consulting GmbH</h2>
    <p class="company__tagline">B2B Sales Consulting</p>
    <p class="company__meta">Business Consulting und Unternehmensdienstleistungen · Kleinhaldern, North Rhine-Westphalia · 1 Follower</p>
    <p class="company__staff">1 Mitarbeiter:in auf Berufora ansehen</p>
  </section>

  <nav class="actions">
    <span class="btn btn--follow">+ Folgen</span>
    <span class="btn btn--website">Website besuchen
      <svg viewBox="0 0 24 24" fill="none" stroke="currentColor" stroke-width="2.4" stroke-linecap="round">
        <path d="M14 3h7v7M21 3l-10 10M18 14v6H4V6h6"/>
      </svg>
    </span>
    <span class="btn btn--more">Mehr</span>
  </nav>
</main>
</body>
</html>
```